Business Card Design and Logo Needed

I need Business Cards and a Logo for my website and public speaking business which can be found at: www.corvina-lett.example

I'm looking for creative and unique ideas. Some business cards I've found online that I like can be found at:
http://gigbarrow.example/general/18-smokin-hot-business-card-designs/

and at

http://www.plumquarry.example/2009/04/50-creative-business-cards-of-50-graphic-designers/

```html
<!DOCTYPE html>
<html lang="en">
<head>
<meta charset="utf-8">
<title>Corvina Lett — Business Card</title>
<link href="https://fonts.googleapis.com/css2?family=Noto+Serif&display=swap" rel="stylesheet">
<style>
  :root {
    --page: #ffffff;
    --card: #201c1a;
    --band: #36312f;
    --tagline: #b5b0ac;
    --name: #ffffff;
    --accent: #f0b400;
    --arrow-1: #5e5a57;
    --arrow-2: #8a8683;
    --arrow-3: #c4c1bf;
    --arrow-4: #ffffff;
  }
  html, body {
    margin: 0;
    padding: 0;
    width: 1200px;
    height: 900px;
    overflow: hidden;
    background: var(--page);
  }
  .canvas {
    position: relative;
    width: 1200px;
    height: 900px;
    font-family: "Noto Serif", Georgia, serif;
  }
  .card {
    position: absolute;
    left: 75px;
    top: 148px;
    width: 1052px;
    height: 602px;
    border-radius: 38px;
    background: var(--card);
    overflow: hidden;
  }
  .name-band {
    position: absolute;
    left: 6px;
    top: 207px;
  }
  .tagline {
    position: absolute;
    left: 3px;
    top: 164px;
    margin: 0;
    font-size: 25px;
    line-height: 1;
    color: var(--tagline);
    white-space: nowrap;
  }
  .brand-dot {
    position: absolute;
    left: 22px;
    top: 278px;
    width: 26px;
    height: 26px;
    border-radius: 50%;
    background: var(--accent);
  }
  .brand-name {
    position: absolute;
    left: 142px;
    top: 230px;
    margin: 0;
    font-size: 92px;
    font-weight: 400;
    line-height: 1;
    color: var(--name);
    letter-spacing: -1px;
    white-space: nowrap;
  }
  .forward-arrows {
    position: absolute;
    left: 778px;
    top: 272px;
    margin: 0;
    font-size: 46px;
    line-height: 1;
    letter-spacing: -4px;
    white-space: nowrap;
  }
  .forward-arrows span:nth-child(1) { color: var(--arrow-1); }
  .forward-arrows span:nth-child(2) { color: var(--arrow-2); }
  .forward-arrows span:nth-child(3) { color: var(--arrow-3); }
  .forward-arrows span:nth-child(4) { color: var(--arrow-4); }
</style>
</head>
<body>
<main class="canvas">
  <section class="card">
    <svg class="name-band" width="1000" height="178" viewBox="0 0 1000 178" aria-hidden="true">
      <path d="M0 0 H860 C940 0 988 44 988 89 C988 134 940 178 860 178 H0 Z" fill="var(--band)"/>
    </svg>
    <p class="tagline">The freedom to live is up to you and the limits of your desires</p>
    <span class="brand-dot" aria-hidden="true"></span>
    <h1 class="brand-name">CorvinaLett</h1>
    <p class="forward-arrows" aria-hidden="true"><span>&gt;</span><span>&gt;</span><span>&gt;</span><span>&gt;</span></p>
  </section>
</main>
</body>
</html>
```